Professional and creative business card design for recruiting service providers

Our company supports German medium-sized companies in filling vacancies promptly. For this we use social media marketing and bring our customers into the visibility.

We want a professional but also creative design for our business cards.

Please look at lindqvar-staff.de to get an impression of our CI.

Target Market(s)

Small and medium-sized companies in Germany from the industry

Industry/Entity Type

Industrie, Handwerk

Contact Information for Business Card

Name, Position, Telefonnummer, Email, Website

Colors
EE7325
F08F49
F5BC92
FAE3D3
FDF4ED

Requirements
Must have
• A picture of the employee and in the style of www.lindqvar-staff.de

```html
<!DOCTYPE html>
<html lang="de">
<head>
<meta charset="utf-8">
<title>Lindqvar &amp; Staff – Visitenkarte</title>
<link rel="stylesheet" href="https://fonts.googleapis.com/css2?family=Montserrat:wght@600;700;800&family=Arimo:wght@400;700&display=swap">
<style>
  :root {
    --orange: #EE7325;
    --orange-light: #F08F49;
    --ink: #1c1c1c;
    --charcoal: #262626;
    --charcoal-deep: #121212;
    --paper: #ffffff;
    --stage: #d4d4d4;
    --text-grey: #2b2b2b;
  }
  * { box-sizing: border-box; margin: 0; padding: 0; }
  html, body { width: 1200px; height: 800px; overflow: hidden; }
  body {
    background: var(--stage);
    display: flex;
    align-items: center;
    justify-content: center;
    gap: 40px;
    font-family: "Arimo", Arial, sans-serif;
  }
  .card {
    position: relative;
    width: 540px;
    height: 310px;
    overflow: hidden;
    border-bottom: 3px solid var(--orange);
    box-shadow: 0 14px 28px rgba(0,0,0,0.22);
  }

  /* Front side */
  .card--front { background: var(--paper); }
  .front__photo {
    position: absolute;
    right: 0; top: 0;
    width: 250px; height: 100%;
    background: linear-gradient(160deg, #f2f2f2 0%, #5a5a60 45%, #2f2f35 100%);
  }
  .front__info {
    position: absolute;
    left: 34px; top: 40px;
    width: 270px;
  }
  .brand {
    display: flex;
    align-items: center;
    gap: 12px;
  }
  .brand__mark {
    width: 34px; height: 34px;
    background: var(--orange);
    flex: none;
  }
  .brand__name {
    font-family: "Montserrat", sans-serif;
    font-weight: 800;
    font-size: 20px;
    line-height: 1.05;
    letter-spacing: 1.5px;
    color: var(--ink);
  }
  .person { margin-top: 42px; }
  .person__name {
    font-family: "Montserrat", sans-serif;
    font-weight: 700;
    font-size: 21px;
    letter-spacing: 1px;
    color: var(--orange);
  }
  .person__role {
    font-size: 14px;
    color: var(--text-grey);
    margin-top: 2px;
  }
  .contacts {
    list-style: none;
    margin-top: 16px;
    font-size: 13.5px;
    color: var(--text-grey);
  }
  .contacts li {
    display: flex;
    align-items: center;
    gap: 9px;
    margin-bottom: 6px;
  }
  .contacts svg { width: 14px; height: 14px; flex: none; }
  .contacts .accent { color: var(--orange); }

  /* Back side */
  .card--back {
    background: var(--charcoal);
  }
  .back__pattern {
    position: absolute; inset: 0;
    background: linear-gradient(200deg, #6a6a6a 0%, #333 40%, var(--charcoal-deep) 100%);
  }
  .back__brand {
    position: absolute;
    right: 44px; bottom: 60px;
  }
  .back__brand .brand__name { color: var(--paper); font-size: 22px; }
  .back__brand .brand__mark { width: 38px; height: 38px; }
</style>
</head>
<body>

  <section class="card card--front" aria-label="Vorderseite">
    <div class="front__photo" role="img" aria-label="Portraitfoto des Mitarbeiters im dunklen Sakko und weißem Hemd"></div>
    <div class="front__info">
      <div class="brand">
        <span class="brand__mark"></span>
        <span class="brand__name">LINDQVAR<br>&amp; STAFF</span>
      </div>
      <div class="person">
        <p class="person__name">MARKUS FELDNER</p>
        <p class="person__role">Managing Director</p>
      </div>
      <ul class="contacts">
        <li>
          <svg viewBox="0 0 24 24" aria-hidden="true"><path fill="var(--orange)" d="M6.6 10.8a15.1 15.1 0 0 0 6.6 6.6l2.2-2.2c.3-.3.7-.4 1-.2 1.1.4 2.3.6 3.6.6.6 0 1 .4 1 1V20c0 .6-.4 1-1 1A17 17 0 0 1 3 4c0-.6.4-1 1-1h3.5c.6 0 1 .4 1 1 0 1.3.2 2.5.6 3.6.1.3 0 .7-.2 1z"/></svg>
          <span>044-987 654 321</span>
        </li>
        <li>
          <svg viewBox="0 0 24 24" aria-hidden="true"><rect x="2" y="5" width="20" height="14" rx="1.5" fill="var(--orange)"/><path d="M3 6l9 7 9-7" fill="none" stroke="#fff" stroke-width="1.8"/></svg>
          <span>info@lindqvar-staff.de</span>
        </li>
        <li>
          <svg viewBox="0 0 24 24" aria-hidden="true"><circle cx="12" cy="12" r="10" fill="var(--orange)"/><path d="M2 12h20M12 2c3 3 3 17 0 20M12 2c-3 3-3 17 0 20M4 7h16M4 17h16" fill="none" stroke="#fff" stroke-width="1.3"/></svg>
          <span>www.<span class="accent">lindqvar-staff</span>.de</span>
        </li>
      </ul>
    </div>
  </section>

  <section class="card card--back" aria-label="Rückseite">
    <div class="back__pattern" role="img" aria-label="Dunkles, glänzendes Muster aus sich wiederholenden Sechseckformen"></div>
    <div class="brand back__brand">
      <span class="brand__mark"></span>
      <span class="brand__name">LINDQVAR<br>&amp; STAFF</span>
    </div>
  </section>

</body>
</html>
```